Wordpress Design ProjectWP website design (Torvald)

We need a wordpress design that will incorporate a professional color scheme with company logo in a clean layout. The design needs to consider that this will be developed on a responsive theme. Colors are undetermined - use a colors in logo - maybe a light color, maybe yellow accent, and black. Client wants a 'modern' look.

Industry/Entity Type

It Company

Font styles to use
Serif
Sans Serif

Requirements
Must have
• Navigation: 1) Home 2) Auctions 3) Services 4) About Us 5) Contact us
• Site will have a slideshow element (initial image attached) and the following widgets: 1)Social Media (facebook,RSS) 2) Email Sign Up Form 3) Featured Video, 4) Auction Search
• Homepage content: "Torvald Auction & Real Estate
• Since 1958 We at Torvald Auction & Real Estate have offered our services to our clients as a versatile Auction Company with the ability to perform a variety of Auction types.
• Having sold Items such as: Real Estate, Machinery, Antiques, Tools, and much, more; we have constructed a strong foundation of knowledge and experience of the appropriate Auction marketing and preparation logistics. This results in a high quality Auction service that we provide to our clients, and also a level of service that we take great pride in.
• When you are ready for your Auction, you want it done right!
• Call Us at Torvald Auction & Real Estate,"
• In the footer, there will be smaller company logo, the affiliations logo (attached), and contact info below:
• Torvald Auction, Inc.
• 5123 County Highway 82
• Walton, NY 14729
• 607-555-0183
Nice to have
• Use of a dropdown menu with styling.

```html
<!DOCTYPE html>
<html lang="en">
<head>
<meta charset="utf-8">
<title>Torvald Auction &amp; Real Estate</title>
<link href="https://fonts.googleapis.com/css2?family=Titillium+Web:wght@400;600&family=Open+Sans:wght@400;600;700&display=swap" rel="stylesheet">
<style>
:root{
  --navy:#15143c;
  --navy-deep:#0d0c26;
  --black:#000;
  --ink:#1c1c1c;
  --muted:#7a7a7a;
  --band:#e7e7e7;
  --blue:#1b64aa;
  --green:#5c7a1e;
  --pink:#e8246f;
  --white:#fff;
}
*{margin:0;padding:0;box-sizing:border-box}
html,body{width:720px;height:1200px;overflow:hidden;background:var(--white)}
body{position:relative;font-family:"Open Sans",Arial,sans-serif;color:var(--ink)}
.abs{position:absolute}
.topline{left:0;top:0;width:720px;height:5px;background:var(--navy)}
.brand{left:60px;top:30px;display:flex;align-items:center;gap:7px;font-family:"Titillium Web",sans-serif;font-weight:600;font-size:22px;color:var(--navy)}
.brand i{width:14px;height:14px;border-radius:50%;background:var(--navy);display:block}
.phones{left:585px;top:28px;font-size:10.5px;line-height:18px;color:var(--ink)}
.phone-icon{left:550px;top:39px}
.nav{left:60px;top:85px;width:600px;height:44px;background:var(--navy)}
.nav a{position:absolute;top:0;height:44px;line-height:44px;font-size:8.5px;font-weight:600;color:var(--white);text-decoration:none;transform:translateX(-50%)}
.nav .active{left:0;width:103px;transform:none;text-align:center;background:var(--black)}
.search{left:455px;top:10px;width:133px;height:24px;background:var(--white);font-size:7px;color:#888;padding:6px 7px}
.search svg{position:absolute;right:10px;top:8px}
.slider{left:60px;top:139px;width:600px;height:301px;background:linear-gradient(180deg,#6f8d5a 0%,#5a7080 45%,#4c5a4a 100%);box-shadow:0 12px 10px -6px rgba(0,0,0,.45)}
.arrow{width:25px;height:25px;border-radius:50%;background:var(--white);top:138px}
.arrow svg{position:absolute;left:8px;top:7px}
.dots{left:268px;top:280px;display:flex;gap:4px}
.dots span{width:8px;height:8px;border-radius:50%;border:1.5px solid var(--white)}
.dots .on{background:var(--blue)}
h2{font-family:"Titillium Web",sans-serif;font-weight:400;color:var(--ink)}
.welcome-title{left:60px;top:468px;font-size:15px}
.welcome-text{left:60px;top:493px;width:330px;font-size:7.4px;line-height:14.4px;color:var(--muted)}
.welcome-text .call{color:var(--ink)}
.btn-dark{background:var(--navy);color:var(--white);font-size:8px;border-radius:2px;text-align:center}
.readmore{left:60px;top:616px;width:79px;height:23px;line-height:23px}
.video{left:411px;top:465px;width:248px;height:173px;background:linear-gradient(135deg,#8fa4c6,#5d79ad 60%,#9eb0cf)}
.play{left:108px;top:70px}
.band{left:0;top:670px;width:720px;height:236px;background:var(--band)}
.auction-title{left:59px;top:686px;font-size:14px}
.pager{left:441px;top:693px}
.card-img{width:186px;height:75px;top:717px}
.card-img.a{left:60px;background:linear-gradient(180deg,#6b8c4a,#8a7f6a)}
.card-img.b{left:273px;background:linear-gradient(180deg,#8fb0d4,#7c8ea3)}
.card-title{top:800px;font-size:8.2px;font-weight:600}
.card-text{top:815px;width:190px;font-size:7.2px;line-height:14px;color:var(--muted)}
.more{top:855px;width:75px;height:22px;line-height:22px;font-weight:700;font-size:7.5px;border-radius:3px}
.panel{left:479px;top:690px;width:180px;height:199px;background:#f4f4f4;border:1px solid #b5b5b5;border-radius:5px;overflow:hidden}
.panel-head{height:32px;background:var(--navy);color:var(--white);font-family:"Titillium Web",sans-serif;font-weight:600;font-size:11px;line-height:32px;padding-left:9px}
.field{position:absolute;left:11px;width:154px;height:24px;background:var(--white);border:1px solid #ddd;font-size:7px;color:#888;padding:6px 8px}
.estimate{position:absolute;left:11px;top:162px;width:154px;height:24px;line-height:24px;background:var(--blue);color:var(--white);text-align:center;font-size:9.5px}
.news-title{left:59px;top:922px;font-size:14px}
.news-dots{left:432px;top:930px;display:flex;gap:2px}
.news-dots span{width:7px;height:7px;border-radius:50%;border:1px solid #333}
.news-dots .on{background:#111}
.thumb{width:76px;height:55px;top:951px;background:linear-gradient(135deg,#3a3530,#c9c2b6)}
.news-item{top:953px;width:120px;font-size:7.2px;line-height:11.5px;color:var(--ink)}
.news-item b{display:block;font-weight:400;color:var(--green)}
.qc-title{left:483px;top:922px;font-size:14px}
.qc-text{left:484px;top:950px;width:180px;font-size:7.2px;line-height:12.5px;color:var(--muted)}
.clickhere{left:484px;top:984px;width:80px;height:23px;line-height:23px;background:linear-gradient(180deg,#2a7cc4,#155694);color:var(--white);font-size:8px;text-align:center;border-radius:2px}
.footer{left:0;top:1034px;width:720px;height:114px;background:var(--navy)}
.footer-bottom{left:0;top:1148px;width:720px;height:52px;background:var(--navy-deep);color:var(--white);font-size:7.5px;text-align:center;line-height:52px}
.fhead{color:var(--white);font-size:7.8px;font-weight:600}
.flist{color:var(--white);font-size:7px;line-height:14.5px}
.badge-round{left:176px;top:1075px;width:62px;height:43px;border-radius:50%;background:var(--white)}
.badge-square{left:248px;top:1077px;width:32px;height:37px;background:var(--white)}
.email-head{left:535px;top:1046px;color:var(--white);font-family:"Titillium Web",sans-serif;font-weight:600;font-size:10.5px}
.email-input{left:535px;top:1067px;width:89px;height:19px;background:var(--white);font-size:6.5px;padding:5px 4px;color:#222}
.send{left:624px;top:1067px;width:37px;height:19px;background:var(--pink);color:var(--white);font-size:7px;font-weight:700;text-align:center;line-height:19px}
.social{top:1098px;width:15px;height:15px;background:#4d6fa8;border-radius:2px}
</style>
</head>
<body>
<div class="abs topline"></div>
<div class="abs brand"><i></i>Torvald</div>
<svg class="abs phone-icon" width="18" height="14" viewBox="0 0 18 14" aria-hidden="true"><path d="M1 5c0-3 16-3 16 0v2h-4V5H5v2H1z M4 7h10l2 6H2z" fill="#222"/></svg>
<div class="abs phones">864) 555-0142<br>(864) 555-0178</div>

<nav class="abs nav">
  <a class="active" href="#">Home</a>
  <a href="#" style="left:145px">Auctions</a>
  <a href="#" style="left:225px">Services</a>
  <a href="#" style="left:306px">About us</a>
  <a href="#" style="left:386px">Contact</a>
  <div class="abs search">Search
    <svg width="8" height="8" viewBox="0 0 8 8" aria-hidden="true"><circle cx="3.2" cy="3.2" r="2.4" fill="none" stroke="#111" stroke-width="1.2"/><path d="M5 5l2.5 2.5" stroke="#111" stroke-width="1.3"/></svg>
  </div>
</nav>

<div class="abs slider" role="img" aria-label="Crowd gathered around a green tractor at an outdoor farm auction">
  <div class="abs arrow" style="left:16px"><svg width="9" height="11" viewBox="0 0 9 11"><path d="M7 1L2 5.5 7 10" fill="none" stroke="#111" stroke-width="2"/></svg></div>
  <div class="abs arrow" style="left:564px"><svg width="9" height="11" viewBox="0 0 9 11"><path d="M2 1l5 4.5L2 10" fill="none" stroke="#111" stroke-width="2"/></svg></div>
  <div class="abs dots"><span class="on"></span><span></span><span></span></div>
</div>

<h2 class="abs welcome-title">Welcome To Torvald Auction &amp; Real Estate</h2>
<p class="abs welcome-text">Since 1958 We at Torvald Auction &amp; Real Estate have offered our services to our clients as a versatile Auction Company with the ability to perform a variety of Auction types. Having sold Items such as: Real Estate, Machinery, Antiques, Tools, and much, more; we have constructed a strong foundation of knowledge and experience of the appropriate Auction marketing and preparation logistics. This results in a high quality Auction service that we provide to our clients, and also a level of service that we take great pride in. When you are ready for your Auction, you want it done right!<br><span class="call">Call Us at Torvald Auction &amp; Real Estate,"</span></p>
<div class="abs btn-dark readmore">Read more</div>

<div class="abs video" role="img" aria-label="Featured video: hand holding house keys">
  <svg class="abs play" width="34" height="34" viewBox="0 0 34 34"><circle cx="17" cy="17" r="16" fill="#d9442c"/><path d="M13 10l11 7-11 7z" fill="#fff"/></svg>
</div>

<div class="abs band"></div>
<h2 class="abs auction-title">Auction</h2>
<svg class="abs pager" width="16" height="10" viewBox="0 0 16 10" aria-hidden="true"><path d="M5 1L1 5l4 4M11 1l4 4-4 4" fill="none" stroke="#111" stroke-width="2"/></svg>
<div class="abs card-img a" role="img" aria-label="Victorian house with a porch among trees"></div>
<div class="abs card-img b" role="img" aria-label="Blue two-storey family house"></div>
<div class="abs card-title" style="left:61px">Duct Cleaning and Air Vents</div>
<div class="abs card-title" style="left:275px">Carpet Cleaning, Area Rugs</div>
<p class="abs card-text" style="left:61px">Vivamus porttitor g puttrus nisi eleifend libero a tempus libero lectus feugiat felis Morbi diam</p>
<p class="abs card-text" style="left:275px">Vivamus porttitor g puttrus nisi eleifend libero a tempus libero lectus feugiat felis Morbi diam</p>
<div class="abs btn-dark more" style="left:60px">READ MORE</div>
<div class="abs btn-dark more" style="left:274px">READ MORE</div>

<form class="abs panel">
  <div class="panel-head">Auction Search</div>
  <div class="field" style="top:39px">Name</div>
  <div class="field" style="top:72px">Phone No</div>
  <div class="field" style="top:103px">E Mail</div>
  <div class="field" style="top:132px">Job details</div>
  <div class="estimate">Free Estimate</div>
</form>

<h2 class="abs news-title">Latest News</h2>
<div class="abs news-dots"><span class="on"></span><span></span><span></span></div>
<div class="abs thumb" style="left:59px" role="img" aria-label="Dimly lit modern interior"></div>
<div class="abs thumb" style="left:270px" role="img" aria-label="Office room with a desk and chair"></div>
<div class="abs news-item" style="left:143px"><b>Lorem ipsum dolor sit amet</b>Lorem ipsum dolor sit amet, consetetur sadipscing elitr, sed diam nonumy eirmod tempor</div>
<div class="abs news-item" style="left:354px"><b>Lorem ipsum dolor sit amet</b>Lorem ipsum dolor sit amet, consetetur sadipscing elitr, sed diam nonumy eirmod tempor</div>
<h2 class="abs qc-title">Quick Contact</h2>
<p class="abs qc-text">Nunc tempus felis vitae urna Vivamus porttitor g purus nisi eleifend libero a tempus libero lectus</p>
<div class="abs clickhere">CLICK HERE</div>

<footer class="abs footer"></footer>
<div class="abs fhead" style="left:60px;top:1047px">Services</div>
<div class="abs flist" style="left:60px;top:1065px">Start Your Campaign<br>Pricing<br>Campaign Playbook<br>Campaign Support</div>
<div class="abs fhead" style="left:178px;top:1047px">Meer halvorsen.Nl</div>
<div class="abs badge-round"></div>
<div class="abs badge-square"></div>
<div class="abs fhead" style="left:325px;top:1047px">Contact Us Today</div>
<div class="abs flist" style="left:325px;top:1065px">TOLL-FREE: (866) 555-0119<br>4410 E, Birchwood Park Blvd, Ste 210<br>Fort Lauderdale, FL 33399<br>Local number: 1-954-555-0163<br>Fax number: 1-954-555-0187</div>
<div class="abs email-head">Email Sign Up Form</div>
<div class="abs email-input">Email address</div>
<div class="abs send">Send</div>
<div class="abs social" style="left:535px"></div>
<div class="abs social" style="left:556px"></div>
<div class="abs social" style="left:576px"></div>
<div class="abs social" style="left:596px"></div>
<div class="abs footer-bottom">Copyright © Torvald All rights reserved.</div>
</body>
</html>
```